Exciting product design for natural pet treats

We need a design for our stand up doy style pouch that blends well with our current logo and also bold enough to stand out from the crowd.

We have a range of natural, Australian made pet treats and need a generic bag that allows for a sticker to be placed on the bag to idenfity the name, while also allowing a space for another sticker on the back for ingredients.
___
Information for the front is: logo, Australian made and owned, Pet Food Only (this is a small font and should not be hero text), 100% Natural, Visit our web site for more amazing products for your pets, Space for sticker 100 - 150mm x 30mm.
___
Information for the back is: Tailwag Depot is proudly Australian owned and operated. We source all our Tailwag Depot treats from reputable suppliers around Australia.

Our Tailwag Depot treats can be purchased through our online store, where you will find a growing range of other brands and products for your dogs, cats, birds, fish, rabbits, guinea pigs, horses, cows, sheep, chickens and more.

For further information, please visit our web site www.tailwagdepot.com.au or email us directly info@tailwagdepot.com.au.
____
The design will be used on three different bag sizes, so our printer can reduce the design from the largest size, but please keep in mind the sizes are 280mm x 380mm, 190mm x 275mm & 160mm x 230mm.

Target Market(s)

Mostly female, 25 to 65 years of age. Pet Lovers, particuarly focussing on dogs.

Industry/Entity Type

pet industry

Requirements
Must have
• Space for sticker on front for the product name 100mm x 30mm. Also a
Nice to have
• Space for a window.
Should not have
• comical pet images. Does not need an image of a pet. Does not need an image of the food.

```html
<!DOCTYPE html>
<html lang="en">
<head>
<meta charset="utf-8">
<title>Tailwag Depot – Treat Pouch, Front and Back</title>
<link rel="stylesheet" href="https://fonts.googleapis.com/css2?family=Oswald:wght@300;400;500&family=Josefin+Sans:wght@300;600&display=swap">
<style>
  :root {
    --bg: #ecebe8;
    --pouch: #3f9fab;
    --pouch-light: #5bb8c3;
    --pouch-dark: #2f8a96;
    --seal: #4aaab6;
    --purple: #4b2a7f;
    --purple-soft: #6a3fa8;
    --white: #ffffff;
    --line: rgba(75, 42, 127, 0.7);
    --treat: #7a5a3a;
    --treat-light: #a4825c;
  }
  * { box-sizing: border-box; margin: 0; padding: 0; }
  html, body { width: 1200px; height: 800px; overflow: hidden; }
  body {
    background: var(--bg);
    font-family: "Oswald", "Arial Narrow", sans-serif;
    color: var(--white);
    position: relative;
  }
  .pouch {
    position: absolute;
    top: 50px;
    width: 420px;
    height: 700px;
    background: linear-gradient(160deg, var(--pouch-light) 0%, var(--pouch) 45%, var(--pouch-dark) 100%);
    border-radius: 6px 6px 14px 14px;
    box-shadow: 0 12px 30px rgba(0,0,0,0.15);
    overflow: hidden;
  }
  .pouch--front { left: 150px; }
  .pouch--back { left: 630px; }
  .pouch__seal {
    position: absolute; left: 0; right: 0; top: 0; height: 70px;
    background: var(--seal);
    border-bottom: 2px solid rgba(255,255,255,0.18);
  }
  .pouch__zip {
    position: absolute; left: 0; right: 0; top: 84px; height: 3px;
    background: rgba(0,0,0,0.08);
  }
  .brand {
    position: absolute; left: 0; right: 0;
    display: flex; align-items: center; justify-content: center; gap: 12px;
  }
  .brand__dot {
    width: 40px; height: 40px; border-radius: 50%;
    border: 3px solid var(--white);
  }
  .brand__name {
    font-family: "Oswald", "Arial Narrow", sans-serif;
    font-weight: 500;
    font-size: 44px;
    color: var(--purple);
    letter-spacing: 0.5px;
  }
  .pouch--front .brand { top: 120px; flex-direction: column; gap: 10px; }
  .pouch--front .brand__dot { width: 70px; height: 70px; }
  .tagline {
    position: absolute; left: 0; right: 0; top: 262px;
    text-align: center;
    font-family: "Josefin Sans", sans-serif; font-weight: 300;
    font-size: 15px; letter-spacing: 1px;
  }
  .sticker-box {
    position: absolute;
    border: 2px dashed var(--line);
    border-radius: 18px;
  }
  .pouch--front .sticker-box { left: 120px; top: 295px; width: 180px; height: 140px; }
  .window { position: absolute; left: 95px; top: 452px; width: 230px; height: 90px; }
  .cta {
    position: absolute; left: 0; right: 0; top: 555px;
    text-align: center; font-size: 18px; line-height: 1.3;
    text-transform: uppercase; font-weight: 400;
  }
  .url-pill {
    position: absolute; left: 105px; top: 615px; width: 210px; height: 30px;
    background: var(--purple); border-radius: 15px;
    display: flex; align-items: center; justify-content: center;
    font-size: 14px; letter-spacing: 0.5px; text-transform: uppercase;
  }
  .natural {
    position: absolute; right: 26px; bottom: 18px;
    display: flex; flex-direction: column; align-items: center;
    font-family: "Josefin Sans", sans-serif; font-weight: 600;
    font-size: 13px; line-height: 1.1; text-transform: uppercase;
  }
  .natural small { font-size: 9px; letter-spacing: 1px; }
  .pouch--back .brand { top: 118px; }
  .pouch--back .brand__name { font-size: 40px; }
  .proudly {
    position: absolute; left: 0; right: 0; top: 178px; text-align: center;
    font-family: "Josefin Sans", sans-serif; font-weight: 600;
    font-size: 11px; letter-spacing: 1px; color: var(--purple-soft);
    text-transform: uppercase;
  }
  .source {
    position: absolute; left: 24px; right: 24px; top: 198px; text-align: center;
    font-size: 18px; line-height: 1.25; text-transform: uppercase; font-weight: 400;
  }
  .ingredients-label {
    position: absolute; left: 0; right: 0; top: 284px; text-align: center;
    font-family: "Josefin Sans", sans-serif; font-weight: 600;
    font-size: 11px; letter-spacing: 1px; color: var(--purple-soft);
    text-transform: uppercase;
  }
  .pouch--back .sticker-box { left: 95px; top: 302px; width: 230px; height: 185px; }
  .about {
    position: absolute; left: 34px; right: 34px; top: 502px; text-align: center;
    font-size: 15px; line-height: 1.35; text-transform: uppercase; font-weight: 300;
  }
  .contact {
    position: absolute; left: 30px; right: 30px; top: 620px; text-align: center;
    font-size: 14px; line-height: 1.4; text-transform: uppercase; font-weight: 300;
  }
</style>
</head>
<body>

<section class="pouch pouch--front" aria-label="Pouch front">
  <div class="pouch__seal"></div>
  <div class="pouch__zip"></div>
  <div class="brand">
    <span class="brand__dot"></span>
    <span class="brand__name">Tailwag Depot</span>
  </div>
  <p class="tagline">PET FOOD ONLY</p>
  <div class="sticker-box" aria-label="Space for product name sticker"></div>
  <svg class="window" viewBox="0 0 230 90" role="img" aria-label="Bone-shaped clear window showing the treats inside">
    <defs>
      <linearGradient id="treatFill" x1="0" y1="0" x2="1" y2="1">
        <stop offset="0" stop-color="var(--treat-light)"/>
        <stop offset="1" stop-color="var(--treat)"/>
      </linearGradient>
    </defs>
    <g fill="url(#treatFill)">
      <circle cx="26" cy="26" r="22"/>
      <circle cx="26" cy="64" r="22"/>
      <circle cx="204" cy="26" r="22"/>
      <circle cx="204" cy="64" r="22"/>
      <rect x="26" y="26" width="178" height="38" rx="4"/>
    </g>
  </svg>
  <p class="cta">Visit our web site for more<br>amazing products for your pets</p>
  <div class="url-pill">www.tailwagdepot.com.au</div>
  <div class="natural">
    <svg width="18" height="20" viewBox="0 0 18 20" aria-hidden="true">
      <path d="M9 19 C9 12 4 9 2 2 C10 3 15 8 9 19 Z" fill="var(--white)"/>
    </svg>
    100%<small>Natural</small>
  </div>
</section>

<section class="pouch pouch--back" aria-label="Pouch back">
  <div class="pouch__seal"></div>
  <div class="pouch__zip"></div>
  <div class="brand">
    <span class="brand__dot"></span>
    <span class="brand__name">Tailwag Depot</span>
  </div>
  <p class="proudly">Proudly Australian owned and operated</p>
  <p class="source">We source all our Tailwag Depot treats from reputable suppliers around Australia.</p>
  <p class="ingredients-label">Ingredients:</p>
  <div class="sticker-box" aria-label="Space for ingredients sticker"></div>
  <p class="about">Our Tailwag Depot treats can be purchased through our online store, where you will find a growing range of other brands and products for your dogs, cats, birds, fish, rabbits, guinea pigs, horses, cows, sheep, chickens and more.</p>
  <p class="contact">For further information:<br>Please visit our web site www.tailwagdepot.com.au or<br>email us directly info@tailwagdepot.com.au.</p>
</section>

</body>
</html>
```